RTavenor Business Cards & Letterhead

I have a logo but need a design for some new business cards. We are a Design-Build Firm that specializes in the design and construction of commercial projects.
the cards need to be professional. no cartoon stuff.
i would like to have the cards in AI format so I can update the card as needed. Logo is provided.
Our Address is: 4187 Marlowe Ct. Ashbury Falls, Norland 27614

```html
<!DOCTYPE html>
<html lang="en">
<head>
<meta charset="utf-8">
<title>RTavenor Business Card</title>
<link href="https://fonts.googleapis.com/css2?family=Montserrat:wght@400;500;700;800&display=swap" rel="stylesheet">
<style>
  :root {
    --stage: #e6e7e9;
    --paper: #ffffff;
    --ink: #222222;
    --charcoal: #212121;
    --brand-blue: #1a7abf;
    --logo-blue: #1560a6;
  }
  * { box-sizing: border-box; margin: 0; padding: 0; }
  html, body { width: 1200px; height: 1059px; overflow: hidden; }
  body {
    background: var(--stage);
    font-family: "Montserrat", sans-serif;
    position: relative;
  }
  .card {
    position: absolute;
    width: 690px;
    height: 392px;
    border-radius: 20px;
    overflow: hidden;
    box-shadow: 0 10px 24px rgba(0,0,0,0.25);
  }
  .card--front { left: 255px; top: 100px; background: var(--paper); }
  .card--back { left: 255px; top: 540px; background: var(--charcoal); }

  .wordmark {
    position: absolute;
    left: 0; right: 0;
    display: flex;
    justify-content: center;
    align-items: center;
    gap: 14px;
    font-weight: 800;
    letter-spacing: 1px;
    white-space: nowrap;
  }
  .wordmark__square { width: 38px; height: 38px; background: var(--logo-blue); }
  .card--front .wordmark { top: 88px; font-size: 58px; color: var(--ink); }
  .card--back .wordmark { top: 160px; font-size: 62px; color: #ffffff; }
  .card--back .wordmark__square { width: 42px; height: 42px; }

  .person {
    position: absolute;
    right: 378px;
    top: 218px;
    text-align: right;
  }
  .person__name {
    font-weight: 700;
    font-size: 26px;
    color: var(--brand-blue);
    letter-spacing: 1px;
    line-height: 1;
  }
  .person__role {
    margin-top: 4px;
    font-size: 17px;
    color: var(--ink);
    letter-spacing: 1px;
  }
  .divider {
    position: absolute;
    left: 343px; top: 212px;
    width: 2px; height: 64px;
    background: var(--brand-blue);
  }
  .contact {
    position: absolute;
    left: 373px; top: 206px;
    list-style: none;
  }
  .contact__item {
    display: flex; align-items: center; gap: 8px;
    height: 26px;
    font-size: 16px;
    color: var(--ink);
    letter-spacing: 0.4px;
  }
  .contact__item svg { width: 13px; height: 13px; fill: var(--brand-blue); }
  .address {
    position: absolute;
    left: 0; right: 0; top: 317px;
    text-align: center;
    font-size: 16px;
    color: var(--ink);
    letter-spacing: 0.4px;
    white-space: nowrap;
  }
  .edge-band { position: absolute; left: 0; bottom: 0; width: 690px; height: 14px; }
</style>
</head>
<body>
  <section class="card card--front">
    <div class="wordmark"><span class="wordmark__square"></span><span>RTAVENOR</span></div>

    <div class="person">
      <p class="person__name">DARRYN COLE</p>
      <p class="person__role">MANAGER</p>
    </div>
    <div class="divider"></div>
    <ul class="contact">
      <li class="contact__item">
        <svg viewBox="0 0 24 24"><path d="M6.6 10.8a15.1 15.1 0 0 0 6.6 6.6l2.2-2.2a1 1 0 0 1 1-.25 11.4 11.4 0 0 0 3.6.57 1 1 0 0 1 1 1V20a1 1 0 0 1-1 1A17 17 0 0 1 3 4a1 1 0 0 1 1-1h3.5a1 1 0 0 1 1 1c0 1.250.2 2.450.57 3.6a1 1 0 0 1-.25 1z"/></svg>
        <span>123-456-7890</span>
      </li>
      <li class="contact__item">
        <svg viewBox="0 0 24 24"><path d="M2 5h20v2l-10 6L2 7z M2 9l10 6 10-6v10H2z"/></svg>
        <span>info@youremail.com</span>
      </li>
      <li class="contact__item">
        <svg viewBox="0 0 24 24"><path d="M12 2a10 10 0 1 0 0 20 10 10 0 0 0 0-20zm0 2c.9 1.2 1.6 2.8 1.9 4.5h-3.8C10.4 6.8 11.1 5.2 12 4zM4.3 13.5a8 8 0 0 1 0-3h3.6a16 16 0 0 0 0 3zm.8 2h3.1c.3 1.4.8 2.7 1.5 3.8a8 8 0 0 1-4.6-3.8zm3.1-7H5.1a8 8 0 0 1 4.6-3.8c-.7 1.1-1.2 2.4-1.5 3.8zM12 20c-.9-1.2-1.6-2.8-1.9-4.5h3.8c-.3 1.7-1 3.3-1.9 4.5zm2.2-6.5H9.8a14 14 0 0 1 0-3h4.4a14 14 0 0 1 0 3zm.1 5.8c.7-1.1 1.2-2.4 1.5-3.8h3.1a8 8 0 0 1-4.6 3.8zm1.8-5.8a16 16 0 0 0 0-3h3.6a8 8 0 0 1 0 3zm-.3-5c-.3-1.4-.8-2.7-1.5-3.8a8 8 0 0 1 4.6 3.8z"/></svg>
        <span>www.yourwebsite.com</span>
      </li>
    </ul>

    <p class="address">4187 Marlowe Ct. Ashbury Falls, Norland 27614</p>

    <svg class="edge-band" viewBox="0 0 690 14" preserveAspectRatio="none">
      <polygon points="0,0 350,0 336,14 0,14" style="fill: var(--brand-blue)"/>
      <polygon points="362,0 690,0 690,14 348,14" style="fill: var(--charcoal)"/>
    </svg>
  </section>

  <section class="card card--back">
    <div class="wordmark"><span class="wordmark__square"></span><span>RTAVENOR</span></div>
  </section>
</body>
</html>
```